13 Varno - new website design project

Our company Varno Electrical is developing a new lead generation website focused on Electrical, LED Lighting and Solar Power. We need a high converting website.

Example of our current website is www.varnoelectrical-example.com.au You can take content from this website for this new design. Our colours are red, black and white. For our new website we would like to promote Varno, Spark Every Day. Please listen to the jingle.

The below link is the company jingle that we have developed.
http://www.tunecraftdemo.com.au/vrn-tc-v1/

The key for this brief is to generate leads for Electrical, LED Lighting (for commercial) and Solar Power & Storage.

Target Market(s)

Business owners in Melbourne Victoria

Number of Pages Required

4 page

Colors
ec1f27
ffffff

Requirements
Must have
• This page must be clean, be in line with company branding and a high converting lead website.

```html
<!DOCTYPE html>
<html lang="en">
<head>
<meta charset="utf-8">
<title>Varno Electrical – Spark Every Day</title>
<link href="https://fonts.googleapis.com/css2?family=Lato:ital,wght@0,400;0,700;0,900;1,400;1,700&family=Open+Sans:wght@400;600;700&display=swap" rel="stylesheet">
<style>
:root{
  --red:#ec1f27;
  --red-dark:#c4141b;
  --ink:#222222;
  --text:#555555;
  --muted:#777777;
  --line:#dddddd;
  --white:#ffffff;
  --grey-band:#e4e4e4;
  --dark:#34363b;
}
*{margin:0;padding:0;box-sizing:border-box}
html,body{width:1200px;height:2528px;overflow:hidden;background:var(--white)}
body{position:relative;font-family:"Open Sans",Arial,sans-serif;color:var(--text)}
.abs{position:absolute}
a{color:inherit;text-decoration:none}

/* header */
.top-rule{left:0;top:0;width:1200px;height:4px;background:linear-gradient(90deg,var(--red) 0 55%,var(--dark) 55%)}
.brand{left:100px;top:12px;width:140px;height:74px;display:flex;align-items:center;gap:8px}
.brand-mark{width:22px;height:22px;background:var(--red);border-radius:50%;flex:none}
.brand-name{font-family:"Lato",sans-serif;font-weight:900;font-size:34px;color:var(--ink);line-height:1}
.brand-tag{font-family:"Lato",sans-serif;font-weight:700;font-size:11px;color:var(--ink);margin-top:3px}
.contact-bar{right:100px;top:14px;display:flex;gap:28px;font-family:"Lato",sans-serif;font-weight:700;font-size:15px;color:var(--ink);align-items:center}
.contact-bar span{display:flex;align-items:center;gap:10px}
.ring{width:32px;height:32px;border:1px solid var(--line);border-radius:50%;display:flex;align-items:center;justify-content:center}
.nav{right:100px;top:64px;display:flex;gap:38px;font-family:"Lato",sans-serif;font-weight:700;font-size:14px;color:var(--ink);align-items:center}
.nav .active{color:var(--red)}

/* hero */
.hero{left:0;top:95px;width:1200px;height:430px;background:linear-gradient(180deg,#3e4a58 0%,#8a7a5e 38%,#e2b15a 55%,#5d6a42 72%,#2b3326 100%)}
.hero-shade{left:0;top:95px;width:1200px;height:430px;background:radial-gradient(ellipse at 50% 62%,rgba(255,220,140,.45),rgba(0,0,0,.15) 60%)}
.hero-title{left:0;top:195px;width:1200px;text-align:center;font-family:"Lato",sans-serif;font-weight:700;font-size:62px;color:var(--white);text-shadow:0 2px 6px rgba(0,0,0,.35)}
.hero-sub{left:0;top:278px;width:1200px;text-align:center;font-family:"Lato",sans-serif;font-size:19px;line-height:33px;color:var(--white);text-shadow:0 1px 4px rgba(0,0,0,.4)}
.btn{display:inline-block;background:var(--red);color:var(--white);font-family:"Lato",sans-serif;font-weight:700;font-size:15px;letter-spacing:.3px;clip-path:polygon(0 0,100% 0,100% 100%,0 100%);position:relative}
.btn::after{content:"";position:absolute;right:0;top:0;width:34px;height:100%;background:var(--ink);clip-path:polygon(0 0,100% 100%,0 100%)}
.hero-btn{left:501px;top:371px;width:198px;height:39px;line-height:39px;text-align:center}
.dots{left:530px;top:485px;display:flex;gap:8px}
.dots i{display:block;width:32px;height:4px;background:var(--white)}
.dots i:first-child{background:var(--red)}

/* welcome */
.welcome h1{position:absolute;left:98px;top:600px;font-family:"Lato",sans-serif;font-weight:700;font-size:28px;color:var(--ink)}
.welcome p{position:absolute;left:98px;width:480px;font-size:12.5px;line-height:24px;color:var(--text)}
.welcome .p1{top:662px}
.welcome .p2{top:780px}
.read-more{font-family:"Lato",sans-serif;font-weight:700;font-size:12.5px;color:var(--red)}
.welcome .read-more{position:absolute;left:98px;top:858px}
.video{left:620px;top:584px;width:482px;height:313px;border:1px solid var(--line);background:var(--white);padding:4px}
.video-frame{width:100%;height:100%;background:linear-gradient(135deg,#c9ccd1 0%,#8e96a3 40%,#2d3a66 70%,#3d4a75 100%);position:relative}
.video-bar{position:absolute;left:0;top:0;width:100%;height:30px;background:rgba(0,0,0,.75);color:var(--white);font-family:"Lato",sans-serif;font-weight:700;font-size:15px;line-height:30px;padding-left:10px}
.play{position:absolute;left:214px;top:128px;width:46px;height:46px;border-radius:50%;background:rgba(20,20,20,.85)}
.play::after{content:"";position:absolute;left:18px;top:14px;border-left:14px solid var(--white);border-top:9px solid transparent;border-bottom:9px solid transparent}

/* services */
.services{left:0;top:963px;width:1200px;height:344px;background:linear-gradient(180deg,#6b6d70 0%,#8a8c90 45%,#5f6164 100%)}
.services-tint{left:0;top:963px;width:1200px;height:344px;background:rgba(40,40,40,.35)}
.services-red{left:350px;top:963px;width:500px;height:344px;background:var(--red);clip-path:polygon(13% 0,100% 0,87% 100%,0 100%)}
.service{width:300px;text-align:center;color:var(--white)}
.service h3{font-family:"Lato",sans-serif;font-weight:700;font-size:19px;margin:18px 0 12px}
.service p{font-size:12.5px;line-height:24px}
.service .read-more{display:block;margin-top:14px;color:var(--white)}
.s1{left:50px;top:1005px}.s2{left:450px;top:1005px}.s3{left:858px;top:1005px}

/* why */
.section-title{left:0;width:1200px;text-align:center;font-family:"Lato",sans-serif;font-weight:700;font-size:26px;color:var(--ink)}
.why-title{top:1360px}
.feature{width:210px;text-align:center}
.feature .circle{width:98px;height:98px;margin:0 auto;border:1px solid #cfcfcf;border-radius:50%;display:flex;align-items:center;justify-content:center}
.feature h4{font-family:"Lato",sans-serif;font-weight:400;font-size:17px;color:var(--ink);margin:18px 0 10px}
.feature p{font-size:11.5px;line-height:23px;color:var(--text)}
.f1{left:80px}.f2{left:287px}.f3{left:495px}.f4{left:702px}.f5{left:909px}
.feature{top:1426px}
.divider{left:98px;top:1663px;width:1004px;height:1px;background:#cfcfcf}

/* clients */
.clients-title{top:1702px}
.client{top:1785px;height:110px;display:flex;align-items:center;justify-content:center;gap:10px;font-family:"Lato",sans-serif;font-weight:700;font-size:22px;color:var(--ink)}
.client i{display:block;width:16px;height:16px;background:var(--red)}
.c1{left:120px;width:200px}.c2{left:360px;width:220px}.c3{left:615px;width:210px}.c4{left:860px;width:220px}

/* testimonial */
.testimonial{left:0;top:1910px;width:1200px;height:258px;background:var(--grey-band)}
.avatar{left:108px;top:1977px;width:128px;height:128px;border-radius:50%;border:5px solid var(--white);background:linear-gradient(160deg,#e8d24a 0%,#c9b73c 40%,#6a6d70 100%);box-shadow:0 0 0 1px #cfcfcf}
.t-rule{left:270px;top:1952px;width:1px;height:168px;background:#bdbdbd}
.quote{left:302px;top:1998px;width:790px;font-family:"Lato",sans-serif;font-style:italic;font-size:14px;line-height:31px;color:#333}
.author{left:302px;top:2076px;font-family:"Lato",sans-serif;font-size:17px;color:var(--red)}
.author b{font-weight:700}
.arrow{top:2048px}

/* footer */
.f-brand{left:98px;top:2230px}
.f-brand .brand-name{font-size:62px}
.f-brand .brand-tag{font-size:20px;margin-top:8px}
.f-col h5{font-family:"Lato",sans-serif;font-weight:700;font-size:17px;color:var(--ink);margin-bottom:16px}
.f-info{left:408px;top:2224px}
.f-info li{list-style:none;font-size:11.5px;line-height:32px;color:var(--text)}
.f-news{left:580px;top:2224px;width:255px}
.f-news p{font-size:11.5px;line-height:20px;color:var(--text)}
.email-field{margin-top:10px;height:36px;border-bottom:1px solid #bbb;font-size:11.5px;color:#999;line-height:36px;padding-left:10px}
.sub-btn{margin-top:16px;width:128px;height:33px;line-height:33px;padding-left:14px;font-size:13.5px}
.sub-btn::after{width:26px}
.f-contact{left:914px;top:2224px}
.f-contact .row{display:flex;gap:16px;font-size:11.5px;line-height:20px;color:var(--text);margin-bottom:18px}
.f-contact svg{flex:none;margin-top:2px}

.bottom-red{left:0;top:2462px;width:655px;height:66px;background:var(--red);clip-path:polygon(0 0,96% 0,100% 100%,0 100%)}
.bottom-dark{left:630px;top:2462px;width:570px;height:66px;background:var(--dark);clip-path:polygon(0 0,100% 0,100% 100%,8% 100%)}
.bottom-line{left:0;top:2462px;width:1200px;height:4px;background:linear-gradient(90deg,var(--red) 0 54%,var(--dark) 54%)}
.copyright{left:98px;top:2485px;font-size:11.5px;color:var(--white)}
.social{left:976px;top:2478px;display:flex;gap:9px}
.social i{display:block;width:26px;height:26px;border:1.5px solid var(--white);border-radius:50%}
</style>
</head>
<body>

<header>
  <div class="abs top-rule"></div>
  <div class="abs brand">
    <div class="brand-mark"></div>
    <div>
      <div class="brand-name">VARNO</div>
      <div class="brand-tag">Spark Every Day</div>
    </div>
  </div>
  <div class="abs contact-bar">
    <span><span class="ring"><svg width="14" height="14" viewBox="0 0 24 24"><path fill="#ec1f27" d="M6.6 10.8a15.1 15.1 0 0 0 6.6 6.6l2.2-2.2c.3-.3.7-.4 1-.2 1.1.4 2.3.6 3.6.6.6 0 1 .4 1 1V20c0 .6-.4 1-1 1A17 17 0 0 1 3 4c0-.6.4-1 1-1h3.5c.6 0 1 .4 1 1 0 1.3.2 2.5.6 3.6.1.3 0 .7-.2 1z"/></svg></span>1300 555 018</span>
    <span><span class="ring"><svg width="14" height="12" viewBox="0 0 24 18"><path fill="#ec1f27" d="M0 0h24v2L12 10 0 2zM0 4.5l12 8 12-8V18H0z"/></svg></span>service@varnoelectrical-example.com.au</span>
  </div>
  <nav class="abs nav">
    <a class="active">HOME</a><a>VARNO STORY</a><a>SERVICES</a><a>OUR WORK</a><a>CONTACT US</a>
    <svg width="14" height="14" viewBox="0 0 24 24"><circle cx="10" cy="10" r="7" fill="none" stroke="#222" stroke-width="3"/><path d="M15 15l7 7" stroke="#222" stroke-width="3"/></svg>
  </nav>
</header>

<section>
  <div class="abs hero" role="img" aria-label="Solar panel fields and wind turbines beside power pylons at sunset"></div>
  <div class="abs hero-shade"></div>
  <h2 class="abs hero-title">Spark Every Day</h2>
  <p class="abs hero-sub">Our company Varno Electrical is developing a new lead generation website<br>focused on Electrical, LED Lighting and Solar Power</p>
  <a class="abs btn hero-btn">GET MORE INFO</a>
  <div class="abs dots"><i></i><i></i><i></i><i></i></div>
</section>

<section class="welcome">
  <h1>WELCOME TO VARNO ELECTRICAL</h1>
  <p class="p1">Electrical and Energy Solutions are at the forefront of our company. Varno Electrical has a long history in Electrical, LED Lighting and Solar Power and just like the Cougar, we will strive to be fierce &amp; agile in an effort to exceed our customer's expectations and develop stronger links with all our business partners &amp; community.</p>
  <p class="p2">Varno Electrical is an expert Electrical Company providing services to all Residential and Commercial customers.</p>
  <a class="read-more">READ MORE &gt;&gt;</a>
  <div class="abs video">
    <div class="video-frame" role="img" aria-label="Video still of an electrician in hi-vis workwear fitting ceiling wiring">
      <div class="video-bar">Expert Electricity Contracting</div>
      <div class="play"></div>
    </div>
  </div>
</section>

<section>
  <div class="abs services" role="img" aria-label="Warehouse roof structure photographed in grey tones"></div>
  <div class="abs services-tint"></div>
  <div class="abs services-red"></div>
  <div class="abs service s1">
    <svg width="60" height="60" viewBox="0 0 60 60" fill="none" stroke="#fff" stroke-width="4"><path d="M34 4L20 32h12l-6 24 16-30H30z" fill="#fff" stroke="none"/><path d="M4 30h8M48 30h8M10 12l5 5M50 12l-5 5M10 48l5-5M50 48l-5-5"/></svg>
    <h3>ELECTRICAL</h3>
    <p>Varno Electrical has an expert team that will come to your business, ensuring you get best advice. Book in today to arrange your free</p>
    <a class="read-more">READ MORE &gt;&gt;</a>
  </div>
  <div class="abs service s2">
    <svg width="60" height="60" viewBox="0 0 60 60" fill="none" stroke="#fff" stroke-width="4"><rect x="12" y="4" width="12" height="16" rx="2"/><path d="M15 4V0M21 4V0M18 20v10a12 12 0 1 0 24 0V20"/><path d="M42 4l-6 10h8l-6 10" /><rect x="36" y="20" width="12" height="6"/></svg>
    <h3>LED LIGHTING</h3>
    <p>Varno Electrical has an expert team that will come to your business, ensuring you get best advice. Book in today to arrange your free</p>
    <a class="read-more">READ MORE &gt;&gt;</a>
  </div>
  <div class="abs service s3">
    <svg width="60" height="60" viewBox="0 0 60 60" fill="none" stroke="#fff" stroke-width="3.5"><path d="M22 12a8 8 0 0 1 16 0" /><path d="M30 0v3M18 4l2 3M42 4l-2 3"/><path d="M8 16h44l4 40H4z"/><path d="M6 30h48M5 43h50M22 16l-3 40M38 16l3 40"/></svg>
    <h3>SOLAR POWER</h3>
    <p>Varno Electrical has an expert team that will come to your business, ensuring you get best advice. Book in today to arrange your free</p>
    <a class="read-more">READ MORE &gt;&gt;</a>
  </div>
</section>

<section>
  <h2 class="abs section-title why-title">WHY CHOOSE US?</h2>
  <div class="abs feature f1"><div class="circle"><svg width="34" height="30" viewBox="0 0 34 30"><circle cx="12" cy="17" r="8" fill="none" stroke="#ec1f27" stroke-width="5" stroke-dasharray="3 2.2"/><circle cx="12" cy="17" r="3" fill="#ec1f27"/><circle cx="26" cy="7" r="5" fill="none" stroke="#ec1f27" stroke-width="4" stroke-dasharray="2.5 1.8"/></svg></div><h4>Professional Service</h4><p>When you hire a Varno Electrical Electrician you will get</p></div>
  <div class="abs feature f2"><div class="circle"><svg width="30" height="30" viewBox="0 0 30 30"><rect x="2" y="13" width="6" height="15" fill="#ec1f27"/><path d="M10 13l6-11c3 0 4 2 3 5l-1 5h8c2 0 3 2 2 4l-3 10c-.5 1.5-1.5 2-3 2H10z" fill="#ec1f27"/></svg></div><h4>5 year Guarantee</h4><p>When you hire a Varno Electrical Electrician you will get</p></div>
  <div class="abs feature f3"><div class="circle"><svg width="34" height="24" viewBox="0 0 34 24"><rect x="1" y="1" width="32" height="22" fill="#ec1f27"/><rect x="5" y="5" width="24" height="14" fill="none" stroke="#fff" stroke-width="1.5"/><circle cx="17" cy="12" r="4" fill="#fff"/></svg></div><h4>Value for Money</h4><p>When you hire a Varno Electrical Electrician you will get</p></div>
  <div class="abs feature f4"><div class="circle"><svg width="34" height="32" viewBox="0 0 34 32" fill="none" stroke="#ec1f27" stroke-width="4"><path d="M11 10l6-8 6 8"/><path d="M28 16l4 9H22"/><path d="M10 27H2l5-9"/><path d="M17 2l-3 5M28 25l-3-5M6 18l5 9"/></svg></div><h4>Environmentally friendly</h4><p>When you hire a Varno Electrical Electrician you will get</p></div>
  <div class="abs feature f5"><div class="circle"><svg width="32" height="32" viewBox="0 0 32 32"><circle cx="16" cy="16" r="15" fill="#ec1f27"/><path d="M9 16l5 5 9-10" fill="none" stroke="#fff" stroke-width="3.5"/></svg></div><h4>Fully insured</h4><p>When you hire a Varno Electrical Electrician you will get</p></div>
  <div class="abs divider"></div>
</section>

<section>
  <h2 class="abs section-title clients-title">OUR SATISFIED CLIENTS INCLUDE...</h2>
  <div class="abs client c1"><i></i>Brookway Plumbing</div>
  <div class="abs client c2">Lumina Living</div>
  <div class="abs client c3"><i></i>Outback Trail Stores</div>
  <div class="abs client c4">Golden Bun Burgers</div>
</section>

<section>
  <div class="abs testimonial"></div>
  <svg class="abs arrow" style="left:36px" width="14" height="26" viewBox="0 0 14 26"><path d="M12 2L2 13l10 11" fill="none" stroke="#fff" stroke-width="3"/></svg>
  <svg class="abs arrow" style="left:1148px" width="14" height="26" viewBox="0 0 14 26"><path d="M2 2l10 11L2 24" fill="none" stroke="#fff" stroke-width="3"/></svg>
  <div class="abs avatar" role="img" aria-label="Client storefront photo in a round frame"></div>
  <div class="abs t-rule"></div>
  <p class="abs quote">The service, communication and after sales service of Varno Electrical has been awesome. We would strongly recommend them to any business contemplating upgrading their lighting or any other electrical work.</p>
  <p class="abs author"><b>- Corey Ashdale,</b> <i>Executive Outback Trail Stores</i></p>
</section>

<footer>
  <div class="abs brand f-brand" style="width:auto;height:auto">
    <div>
      <div class="brand-name">VARNO</div>
      <div class="brand-tag">Spark Every Day</div>
    </div>
  </div>
  <div class="abs f-col f-info">
    <h5>Information</h5>
    <ul><li>Home</li><li>Varno Story</li><li>Services</li><li>Our Work</li><li>Contact Us</li></ul>
  </div>
  <div class="abs f-col f-news">
    <h5>Newsletter Subscription</h5>
    <p>Register your Email Address to get Information about us</p>
    <div class="email-field">Email Address</div>
    <a class="btn sub-btn" style="display:block">SUBSCRIBE</a>
  </div>
  <div class="abs f-col f-contact">
    <h5>Contact Us</h5>
    <div class="row"><svg width="10" height="14" viewBox="0 0 10 14"><path d="M5 0a5 5 0 0 1 5 5c0 4-5 9-5 9S0 9 0 5a5 5 0 0 1 5-5z" fill="#ec1f27"/><circle cx="5" cy="5" r="2" fill="#fff"/></svg><span>Unit 4/82 Kellaway Rd<br>Glenbrook East, VIC 3199</span></div>
    <div class="row"><svg width="12" height="12" viewBox="0 0 24 24"><path fill="#ec1f27" d="M6.6 10.8a15.1 15.1 0 0 0 6.6 6.6l2.2-2.2c.3-.3.7-.4 1-.2 1.1.4 2.3.6 3.6.6.6 0 1 .4 1 1V20c0 .6-.4 1-1 1A17 17 0 0 1 3 4c0-.6.4-1 1-1h3.5c.6 0 1 .4 1 1 0 1.3.2 2.5.6 3.6.1.3 0 .7-.2 1z"/></svg><span>1300 555 018</span></div>
    <div class="row"><svg width="13" height="10" viewBox="0 0 24 18"><path fill="#ec1f27" d="M0 0h24v2L12 10 0 2zM0 4.5l12 8 12-8V18H0z"/></svg><span>service@varnoelectrical-example.com.au</span></div>
  </div>
  <div class="abs bottom-dark"></div>
  <div class="abs bottom-red"></div>
  <div class="abs bottom-line"></div>
  <p class="abs copyright">Copyrights © 2017, Varno Electrical. All rights reserved.</p>
  <div class="abs social"><i></i><i></i><i></i><i></i></div>
</footer>

</body>
</html>
```